New Dental Office Needs an Attractive and user friendly Website Designed

I need a website for a new dental office. The Name is Harrowfield Dentistry. I would like a Modern design with a user friendly interface and usability.
I would like a landing page, a page that lists the services we offer: Cosmetic Dentistry, Implants, Dental Hygiene, Emergency Services, Restorations, Dentures
Target Market(s)
Mid to upper class
Industry/Entity Type
Dentistry
Coding
Number of Pages Required
1 page
Requirements
Must have
- Landing page that has a scheduling option, Procedures, operating hours, and contact us info
Nice to have
- Appealing design, Soft comforting colors. Easy to navigate page, Modern and professional.

```html
<!DOCTYPE html>
<html lang="en">
<head>
<meta charset="utf-8">
<title>Harrowfield Dentistry</title>
<link rel="stylesheet" href="https://fonts.googleapis.com/css2?family=Spectral:wght@400;500;600&family=Lato:wght@400;700&display=swap">
<style>
:root{
  --navy:#0b3347;
  --mist:#d8dde0;
  --cream:#efedea;
  --ink:#1b2a33;
  --accent:#2ec4b6;
  --accent-text:#1f8f86;
  --white:#ffffff;
  --serif:"Spectral",Georgia,serif;
  --sans:"Lato",Arial,sans-serif;
}
*{box-sizing:border-box;margin:0;padding:0}
html,body{width:1200px;height:5164px;overflow:hidden}
body{font-family:var(--sans);color:var(--ink);background:var(--white);position:relative}
section,header,footer,.topbar{position:relative;width:1200px}
.abs{position:absolute}
.btn{position:absolute;display:flex;align-items:center;justify-content:center;background:var(--navy);color:var(--white);font-family:var(--sans);font-size:20px;border-radius:3px;text-decoration:none}
.serif-title{font-family:var(--serif);font-weight:500;letter-spacing:2px;color:var(--navy);white-space:nowrap}

.topbar{height:40px;background:var(--navy);color:var(--white);font-size:15px}
.topbar .phone{left:92px;top:11px;display:flex;align-items:center;gap:8px}
.topbar .social{right:90px;top:11px;display:flex;gap:8px}
.topbar .social span{width:18px;height:18px;border-radius:3px;background:var(--white);display:block}

.site-header{height:96px;border-bottom:2px solid #bfe0d4;background:var(--white)}
.brand{left:95px;top:20px;text-align:center;font-family:var(--serif);font-weight:500;color:var(--navy);line-height:1}
.brand .name{font-size:34px;letter-spacing:.5px}
.brand .sub{font-size:15px;letter-spacing:5px;margin-top:3px}
.nav{left:552px;top:36px;font-size:18px;color:var(--navy)}
.nav a{color:var(--navy);text-decoration:none;position:absolute;white-space:nowrap}

.hero{height:530px;background:var(--cream)}
.hero h1{left:88px;top:98px;font-size:54px;line-height:68px;font-weight:600;letter-spacing:1.5px}
.hero p{left:86px;top:252px;font-size:28px;line-height:44px;color:#111}
.hero .photo{left:600px;top:0;width:600px;height:530px;background:linear-gradient(90deg,#ede9e4,#d9d0c6 45%,#2b3a55)}

.about{height:268px;background:var(--mist)}
.about h2{left:86px;top:94px;font-size:50px}
.about p{left:343px;top:90px;font-size:24px;line-height:31px;color:#111}

.services{height:1014px}
.services h2{left:0;width:1200px;text-align:center;top:88px;font-size:50px}
.services .lede{left:0;width:1200px;text-align:center;top:168px;font-size:24px;color:#111}
.card{position:absolute;width:340px;text-align:center}
.card svg{display:block;margin:0 auto;height:86px}
.card h3{font-family:var(--sans);font-size:24px;font-weight:700;color:var(--navy);margin-top:22px;letter-spacing:.3px}
.card p{font-size:16px;line-height:24px;margin-top:8px;color:#111}
.card .btn{position:relative;width:160px;height:50px;margin:29px auto 0}

.cta{height:386px;background:var(--navy);overflow:hidden;color:var(--white)}
.cta h2{left:88px;top:80px;font-size:52px;color:var(--white);font-weight:600}
.cta p{left:88px;top:160px;font-size:24px;line-height:34px}
.cta .btn{left:88px;top:258px;width:157px;height:48px;background:var(--white);color:var(--navy)}

.hours{height:950px}
.hours h2{left:90px;top:92px;font-size:50px;line-height:68px}
.hours-box{left:86px;top:278px;width:470px;height:378px;background:var(--mist);border-radius:16px}
.hours-box table{position:absolute;left:34px;top:40px;border-collapse:collapse;font-size:24px;color:#111}
.hours-box td{height:42.6px;padding:0}
.hours-box td:first-child{width:182px}
.hours address{left:106px;top:696px;font-style:normal;font-size:25px;line-height:32px;color:var(--navy)}
.hours .btn{left:106px;top:784px;width:190px;height:50px}
.hours .photo{left:614px;top:92px;width:499px;height:744px;border-radius:4px;background:linear-gradient(160deg,#cdd4d8,#9aa6ad 50%,#3c4549)}

.reviews{height:582px;background:var(--mist)}
.reviews h2{left:0;width:1200px;text-align:center;top:100px;font-size:50px}
.review{position:absolute;top:214px;width:320px;height:274px;background:var(--white);border-radius:10px;padding:38px 0 0 42px;font-size:19px;line-height:34px;color:#111}
.review .mark{display:block;height:34px;margin-bottom:8px}
.review .who{font-weight:700;margin-top:22px;font-size:19px;color:#111}
.review.highlight{color:var(--accent-text)}

.book{height:552px}
.book h2{left:88px;top:110px;font-size:52px;line-height:70px}
.book p{left:86px;top:276px;font-size:24px;line-height:34px;color:#111}
.book .btn{left:86px;top:388px;width:190px;height:48px}
.book .photo{left:630px;top:0;width:570px;height:552px;background:linear-gradient(90deg,#f1ece4,#d8cbbb 50%,#c9c3bc)}

.newsletter{height:388px;background:var(--mist)}
.newsletter h2{left:0;width:1200px;text-align:center;top:88px;font-size:50px}
.newsletter p{left:0;width:1200px;text-align:center;top:168px;font-size:24px;color:#111}
.newsletter form{position:absolute;left:306px;top:240px;display:flex}
.newsletter input{width:392px;height:58px;border:0;background:var(--white);font-family:var(--sans);font-size:20px;padding-left:36px;color:#111}
.newsletter input::placeholder{color:#111}
.newsletter button{width:196px;height:58px;border:0;background:var(--navy);color:var(--white);font-family:var(--sans);font-size:30px;border-radius:2px}

.site-footer{height:358px;text-align:center}
.site-footer .brand{left:0;width:1200px;top:54px}
.foot-links{left:0;width:1200px;top:144px;font-size:18px;color:var(--navy);display:flex;justify-content:center;gap:48px}
.legal{left:0;width:1200px;top:200px;font-size:18px;color:var(--navy)}
.copy{left:0;width:1200px;top:250px;font-size:18px;color:#111}
</style>
</head>
<body>

<div class="topbar">
  <div class="abs phone">
    <svg width="10" height="18" viewBox="0 0 10 18"><rect x="0.5" y="0.5" width="9" height="17" rx="2" fill="#fff"/></svg>
    (865) 555-0142
  </div>
  <div class="abs social" aria-label="Social links"><span></span><span></span><span></span></div>
</div>

<header class="site-header">
  <div class="abs brand"><div class="name">Harrowfield</div><div class="sub">DENTISTRY</div></div>
  <nav class="abs nav">
    <a href="#services" style="left:0">Services</a>
    <a href="#about" style="left:133px">About</a>
    <a href="#contact" style="left:243px">Contact</a>
  </nav>
  <a class="btn" href="#book" style="left:948px;top:22px;width:167px;height:50px;font-size:21px">Book Online</a>
</header>

<section class="hero">
  <h1 class="abs serif-title">Advance Care with<br>a Gentle Touch</h1>
  <p class="abs">Advanced Care with a Gentle Touch.<br>Because Your Smile Deserves the Best.</p>
  <a class="btn" href="#book" style="left:86px;top:359px;width:269px;height:48px">Schedule Appointment</a>
  <div class="abs photo" role="img" aria-label="Smiling family of three: mother, young son and father"></div>
</section>

<section class="about" id="about">
  <h2 class="abs serif-title">About Us</h2>
  <p class="abs">Providing exceptional dental care in a tranquil, spa-like setting.<br>We cater to your individual needs with state-of-the-art technology<br>and a gentle personal approach.</p>
</section>

<section class="services" id="services">
  <h2 class="abs serif-title">Our Services</h2>
  <p class="abs lede">Comprehensive Dental Solutions, Tailored to You.</p>

  <div class="card" style="left:82px;top:280px">
    <svg viewBox="0 0 80 86" fill="none" stroke="#0b3347" stroke-width="3" stroke-linejoin="round"><path d="M14 14c8-6 18-4 24 0 6-4 14-5 20-2 8 4 9 16 6 28-3 10-4 26-9 38-2 4-6 4-7 0l-4-18c-1-5-7-5-8 0l-4 18c-1 4-5 4-7 0-5-12-6-28-9-38-3-10-3-20-2-26z"/><path d="M62 2l3 8 8 3-8 3-3 8-3-8-8-3 8-3z"/></svg>
    <h3>Cosmetic Dentistry</h3>
    <p>Whitening, veneers, and smile<br>makeovers for a confident appearance.</p>
    <a class="btn" href="#book">Learn More</a>
  </div>
  <div class="card" style="left:430px;top:280px">
    <svg viewBox="0 0 80 86" fill="none" stroke="#0b3347" stroke-width="3" stroke-linejoin="round"><path d="M22 8c6-4 12-2 18 0 6-2 12-4 18 0 5 4 4 12 2 18H20c-2-6-3-14 2-18z"/><path d="M22 30h36M26 38h28M28 46h24M30 54h20M32 62h16M36 70h8"/><path d="M30 30l10 48 10-48"/></svg>
    <h3>Dental Implants</h3>
    <p>Permanent tooth replacement<br>with natural look, feel, and function.</p>
    <a class="btn" href="#book">Learn More</a>
  </div>
  <div class="card" style="left:778px;top:280px">
    <svg viewBox="0 0 86 86" fill="none" stroke="#0b3347" stroke-width="3" stroke-linejoin="round"><path d="M6 74l46-46 8 8-46 46-8 0z"/><path d="M14 70l6 6M22 62l6 6M30 54l6 6"/><path d="M62 26c-4-8 2-18 8-22 4 6 8 16 0 22-3 2-6 2-8 0z"/></svg>
    <h3>Hygiene &amp; Cleanings</h3>
    <p>Thorough, professional cleanings<br>to protect your oral health.</p>
    <a class="btn" href="#book">Learn More</a>
  </div>

  <div class="card" style="left:82px;top:642px">
    <svg viewBox="0 0 80 86" fill="none" stroke="#0b3347" stroke-width="3" stroke-linejoin="round"><path d="M40 6l30 10v24c0 20-14 34-30 40C24 74 10 60 10 40V16z"/><path d="M34 26h12v10h10v12H46v10H34V48H24V36h10z"/></svg>
    <h3>Emergency Services</h3>
    <p>Prompt, compassionate care<br>when dental issues can't wait.</p>
    <a class="btn" href="#book">Learn More</a>
  </div>
  <div class="card" style="left:430px;top:642px">
    <svg viewBox="0 0 80 86" fill="none" stroke="#0b3347" stroke-width="3" stroke-linejoin="round"><path d="M14 12c8-6 18-4 26 0 8-4 18-6 26 0 8 6 6 20 2 30-3 10-4 24-8 34-2 5-7 5-8 0l-5-18c-2-6-12-6-14 0l-5 18c-1 5-6 5-8 0-4-10-5-24-8-34-4-10-6-24 2-30z"/><path d="M22 18c4-3 10-3 14 0"/></svg>
    <h3>Restorations</h3>
    <p>Repair and strengthen teeth<br>with expertly crafted solutions.</p>
    <a class="btn" href="#book">Learn More</a>
  </div>
  <div class="card" style="left:778px;top:642px">
    <svg viewBox="0 0 86 86" fill="none" stroke="#0b3347" stroke-width="3" stroke-linejoin="round"><path d="M6 34c10 4 64 4 74 0 0 10-6 18-14 20H20C12 52 6 44 6 34z"/><path d="M18 38v14M30 40v14M43 40v14M56 40v14M68 38v14"/></svg>
    <h3>Dentures &amp; Partials</h3>
    <p>Custom full or partial dentures<br>designed for comfort and fit.</p>
    <a class="btn" href="#book">Learn More</a>
  </div>
</section>

<section class="cta">
  <h2 class="abs serif-title">Time to Prioritize Yourself.</h2>
  <p class="abs">Book your appointment with Harrowfield Dentistry and experience<br>our calming environment and personalized attention first hand.</p>
  <a class="btn" href="#book">Learn More</a>
</section>

<section class="hours" id="contact">
  <h2 class="abs serif-title">Office Hours<br>&amp; Location</h2>
  <div class="abs hours-box">
    <table>
      <tr><td>Monday</td><td>8:00 AM - 4:30 PM</td></tr>
      <tr><td>Tuesday</td><td>8:00 AM - 4:30 PM</td></tr>
      <tr><td>Wednesday</td><td>Closed</td></tr>
      <tr><td>Thursday</td><td>8:00 AM - 4:30 PM</td></tr>
      <tr><td>Friday</td><td>8:00 AM - 4:30 PM</td></tr>
      <tr><td>Saturday</td><td>Closed</td></tr>
      <tr><td>Sunday</td><td>Closed</td></tr>
    </table>
  </div>
  <address class="abs">2240 Willowmere Lane Ste 12<br>Maryville, TN 37804</address>
  <a class="btn" href="#contact">Get Directions</a>
  <div class="abs photo" role="img" aria-label="Dentist in scrubs and loupes treating a patient in the dental chair"></div>
</section>

<section class="reviews">
  <h2 class="abs serif-title">What Our Patients Are Saying</h2>
  <div class="review" style="left:88px">
    <svg class="mark" width="36" height="28" viewBox="0 0 36 28"><path d="M2 26V14C2 6 7 2 14 1v5c-4 1-6 4-6 7h6v13zM20 26V14c0-8 5-12 12-13v5c-4 1-6 4-6 7h6v13z" fill="#2ec4b6"/></svg>
    The staff is very friendly<br>and professional. Highly<br>recommend this office!
    <div class="who">- Nora P</div>
  </div>
  <div class="review" style="left:440px">
    <svg class="mark" width="36" height="28" viewBox="0 0 36 28"><path d="M2 26V14C2 6 7 2 14 1v5c-4 1-6 4-6 7h6v13zM20 26V14c0-8 5-12 12-13v5c-4 1-6 4-6 7h6v13z" fill="#2ec4b6"/></svg>
    My experience with the<br>Doctor was fantastic.<br>I feel confident in my smile.
    <div class="who">- Caleb T</div>
  </div>
  <div class="review highlight" style="left:792px">
    <svg class="mark" width="36" height="28" viewBox="0 0 36 28"><path d="M2 26V14C2 6 7 2 14 1v5c-4 1-6 4-6 7h6v13zM20 26V14c0-8 5-12 12-13v5c-4 1-6 4-6 7h6v13z" fill="#2ec4b6"/></svg>
    I had an emergency and<br>Got same-day treatment.<br>So grateful for the care!
    <div class="who">- Ivy L</div>
  </div>
</section>

<section class="book" id="book">
  <h2 class="abs serif-title">Book an<br>Appointment</h2>
  <p class="abs">Ready for a healthier smile?<br>Scheduling your visit is quick and easy.</p>
  <a class="btn" href="#book">Schedule Now</a>
  <div class="abs photo" role="img" aria-label="Smiling couple, a man in a teal shirt and a woman in a grey top"></div>
</section>

<section class="newsletter">
  <h2 class="abs serif-title">Subscribe to Our Newsletter</h2>
  <p class="abs">Stay up to date with our latest news and dental tips.</p>
  <form>
    <input type="email" placeholder="Enter your email address" aria-label="Email address">
    <button type="button">Subscribe</button>
  </form>
</section>

<footer class="site-footer">
  <div class="abs brand"><div class="name">Harrowfield</div><div class="sub">DENTISTRY</div></div>
  <nav class="abs foot-links"><span>Home</span><span>Services</span><span>About</span><span>Contact</span></nav>
  <div class="abs legal">Privacy Policy | Terms</div>
  <div class="abs copy">© 2025 Harrowfield Dentistry. All rights reserved.</div>
</footer>

</body>
</html>
```